Lurvik.no is a new website about pedagogical entrepreneurship. It's main target group is teachers. The Nordic Bureau for Digital Schooling and the National Office for Learning and Classrooms are leading the project.

The web page is meant to show examples of how different methods of entrepreneurship can be used pedagogical in a learning environment. The page will also support the user with examples of different teaching programs and other examples of best practice.

Pedagogical entrepreneurship is not about business and men in suits. It's a method for learning. The focus in the design should be on school, education and new ways of learning.

The final product should be motivating and engaging, but at the same time governmental and serious. We are not looking for something "flashy" and corporate-looking, but a moderate, task-focused and clean design that state quality.

We need designs for three pages:
1 - frontpage
2 - subpage ("Metoder og undervisningsopplegg")
3 - subpage ("Små-TOPP i Vassbygd")

The interaction design for these three pages will be uploaded as an attachment.

We would like you to find inspiration in the following websites:
- www.skapekraft.no
- www.giellu.no
- www.brightfernlab.com
- www.zyx.no
(more will be added)

Please use the attached logo, and feel free to use this as an inspiration for the rest of the design.

Target Market(s)

Teachers

Industry/Entity Type

Education

Requirements
Must have
• * Header with: Logo. Main navigation. Utility navigation. Search box.
* Footer
Should not have
• Images of men in suits.
Very strong graphical elements that stands out too much (we want it clean).

```html
<!DOCTYPE html>
<html lang="en">
<head>
<meta charset="utf-8">
<title>Lurvik – Pedagogical entrepreneurship</title>
<link rel="stylesheet" href="https://fonts.googleapis.com/css2?family=Open+Sans:wght@400;600;700&display=swap">
<style>
  :root {
    --navy: #1b4b86;
    --blue: #2a73b5;
    --sky: #4f9bd6;
    --pale: #e3eff9;
    --mist: #f4f8fc;
    --ink: #3a3f47;
    --muted: #6b7480;
    --white: #ffffff;
    --leaf: #3da33a;
  }
  * { box-sizing: border-box; margin: 0; padding: 0; }
  html, body { width: 1200px; height: 900px; overflow: hidden; }
  body {
    font-family: "Open Sans", Arial, sans-serif;
    color: var(--ink);
    background: var(--white);
  }
  .page { position: relative; width: 1200px; height: 900px; overflow: hidden;
    background: linear-gradient(180deg, var(--white) 0%, var(--white) 58%, var(--pale) 72%, var(--mist) 100%); }

  /* utility bar */
  .utility { position: absolute; top: 0; left: 0; right: 0; height: 34px;
    display: flex; justify-content: flex-end; align-items: center; gap: 26px; padding-right: 100px; }
  .utility a { font-size: 12px; font-weight: 600; color: var(--navy); text-decoration: none; }
  .search { width: 190px; height: 24px; background: var(--navy); border-radius: 3px;
    display: flex; align-items: center; justify-content: space-between; padding: 0 8px;
    color: #cfe0f2; font-size: 11px; }

  /* brand */
  .brand { position: absolute; left: 100px; top: 78px; display: flex; align-items: center; gap: 12px; }
  .brand-dot { width: 44px; height: 44px; border-radius: 50%; background: var(--blue); }
  .brand-name { font-size: 46px; font-weight: 600; color: var(--blue); letter-spacing: -1px; }

  /* hero */
  .hero-text { position: absolute; right: 450px; top: 92px; text-align: right; width: 520px; }
  .hero-title { font-size: 24px; font-weight: 700; color: var(--navy); line-height: 1.2; }
  .hero-body { margin-top: 10px; font-size: 14px; color: var(--muted); line-height: 1.5; }
  .hero-photo { position: absolute; right: 100px; top: 40px; width: 340px; height: 250px;
    background: radial-gradient(ellipse at 60% 40%, #efe6d9 0%, #dfe8f1 55%, rgba(255,255,255,0) 80%); }

  /* feature row */
  .features { position: absolute; left: 100px; right: 100px; top: 300px; height: 170px;
    display: grid; grid-template-columns: repeat(3, 1fr); }
  .feature { position: relative; padding: 0 20px; border-left: 2px dotted #bcd3e8; }
  .feature:first-child { border-left: none; padding-left: 0; }
  .feature-head { display: flex; align-items: center; gap: 12px; height: 96px; }
  .feature-icon { flex: none; width: 64px; height: 64px; }
  .feature-title { font-size: 22px; color: var(--navy); line-height: 1.15; }
  .feature-btn { display: inline-flex; align-items: center; gap: 8px; margin-top: 8px;
    background: linear-gradient(180deg, var(--blue), var(--navy)); color: var(--white);
    font-size: 11px; font-weight: 700; padding: 5px 8px 5px 12px; border-radius: 2px; text-transform: uppercase; }
  .feature-btn svg { width: 14px; height: 14px; }

  /* band */
  .band { position: absolute; left: 0; top: 470px; width: 1200px; height: 140px; }

  /* lower panels */
  .panel { position: absolute; background: var(--white); border: 1px solid #c9dbec;
    box-shadow: 0 4px 10px rgba(27,75,134,.18); }
  .panel-tab { height: 34px; background: linear-gradient(180deg, var(--sky), var(--blue));
    color: var(--white); font-size: 17px; font-weight: 600; padding: 5px 14px; }
  .quiz { left: 100px; top: 610px; width: 300px; height: 200px; }
  .quiz-body { display: flex; gap: 14px; padding: 20px 14px; }
  .quiz-icon { width: 64px; height: 64px; flex: none; }
  .quiz h3 { font-size: 22px; color: var(--navy); line-height: 1.1; }
  .quiz p { font-size: 13px; color: var(--muted); margin-top: 6px; line-height: 1.3; }

  .start { left: 430px; top: 560px; width: 670px; height: 250px; display: grid;
    grid-template-rows: 34px 1fr; }
  .start-cols { display: grid; grid-template-columns: 1fr 200px; padding: 14px 18px; }
  .start-cols h3 { font-size: 21px; color: var(--navy); font-weight: 700; }
  .start-cols ul { list-style: none; margin-top: 6px; }
  .start-cols li { font-size: 14px; line-height: 1.55; color: var(--ink); }
  .start-cols li::before { content: "» "; color: var(--blue); font-weight: 700; }
  .methods { border-left: 2px dotted #bcd3e8; padding-left: 18px; }
  .methods li { color: var(--blue); }
</style>
</head>
<body>
<div class="page">

  <nav class="utility">
    <a href="#">Best practice schools</a>
    <a href="#">Newsletter</a>
    <a href="#">About Lurvik</a>
    <div class="search"><span>Search for...</span>
      <svg width="12" height="12" viewBox="0 0 12 12"><circle cx="5" cy="5" r="3.6" fill="none" stroke="#fff" stroke-width="1.6"/><line x1="7.7" y1="7.7" x2="11" y2="11" stroke="#fff" stroke-width="1.8"/></svg>
    </div>
  </nav>

  <div class="brand"><span class="brand-dot"></span><span class="brand-name">Lurvik</span></div>

  <div class="hero-photo" role="img" aria-label="Photo of smiling teachers holding books"></div>
  <div class="hero-text">
    <h1 class="hero-title">Pedagogical<br>entrepreneurship works.</h1>
    <p class="hero-body">Lorem ipsum dolor sit amet, consectetur adipiscing elit.<br>Consectetur adipiscing elit dolor sit dolor sit lorem ipsum.</p>
  </div>

  <section class="features">
    <div class="feature">
      <div class="feature-head">
        <svg class="feature-icon" viewBox="0 0 64 64" aria-hidden="true">
          <circle cx="38" cy="26" r="18" fill="none" stroke="var(--blue)" stroke-width="5"/>
          <line x1="25" y1="39" x2="8" y2="56" stroke="var(--navy)" stroke-width="8" stroke-linecap="round"/>
          <circle cx="38" cy="21" r="5" fill="var(--sky)"/>
          <path d="M29 35 q9 -12 18 0" fill="var(--sky)"/>
        </svg>
        <h2 class="feature-title">What is pedagogical entrepreneurship?</h2>
      </div>
      <span class="feature-btn">Learn about what, why and how!
        <svg viewBox="0 0 14 14"><rect width="14" height="14" fill="#fff"/><path d="M5 3 l4 4 -4 4" fill="none" stroke="var(--navy)" stroke-width="2"/></svg></span>
    </div>
    <div class="feature">
      <div class="feature-head">
        <svg class="feature-icon" viewBox="0 0 64 64" aria-hidden="true">
          <line x1="12" y1="48" x2="30" y2="34" stroke="var(--blue)" stroke-width="3"/>
          <line x1="30" y1="34" x2="50" y2="14" stroke="var(--blue)" stroke-width="3"/>
          <line x1="30" y1="34" x2="52" y2="40" stroke="var(--blue)" stroke-width="3"/>
          <circle cx="12" cy="48" r="7" fill="#fff" stroke="var(--blue)" stroke-width="4"/>
          <circle cx="30" cy="34" r="7" fill="#fff" stroke="var(--blue)" stroke-width="4"/>
          <circle cx="50" cy="14" r="7" fill="#fff" stroke="var(--blue)" stroke-width="4"/>
          <circle cx="52" cy="40" r="6" fill="#fff" stroke="var(--blue)" stroke-width="4"/>
        </svg>
        <h2 class="feature-title">Methods and teaching plans</h2>
      </div>
      <span class="feature-btn">Plan your lessons!
        <svg viewBox="0 0 14 14"><rect width="14" height="14" fill="#fff"/><path d="M5 3 l4 4 -4 4" fill="none" stroke="var(--navy)" stroke-width="2"/></svg></span>
    </div>
    <div class="feature">
      <div class="feature-head">
        <div class="feature-icon" role="img" aria-label="Illustration of a green sprout" style="background:radial-gradient(circle at 50% 45%, var(--leaf) 0%, #7cc46a 50%, rgba(255,255,255,0) 72%);"></div>
        <h2 class="feature-title">Good examples, best practice</h2>
      </div>
      <span class="feature-btn">Be inspired!
        <svg viewBox="0 0 14 14"><rect width="14" height="14" fill="#fff"/><path d="M5 3 l4 4 -4 4" fill="none" stroke="var(--navy)" stroke-width="2"/></svg></span>
    </div>
  </section>

  <svg class="band" viewBox="0 0 1200 140" preserveAspectRatio="none" aria-hidden="true">
    <defs>
      <linearGradient id="bandFill" x1="0" y1="0" x2="0" y2="1">
        <stop offset="0" stop-color="#4f9bd6"/>
        <stop offset="1" stop-color="#e3eff9" stop-opacity="0"/>
      </linearGradient>
    </defs>
    <path d="M0 60 C300 20 700 100 1200 40 L1200 140 L0 140 Z" fill="url(#bandFill)"/>
    <path d="M0 60 C300 20 700 100 1200 40" fill="none" stroke="#ffffff" stroke-width="3" opacity=".8"/>
  </svg>

  <section class="panel quiz">
    <div class="panel-tab">Test yourself!</div>
    <div class="quiz-body">
      <svg class="quiz-icon" viewBox="0 0 64 64" aria-hidden="true">
        <path d="M8 44 A24 24 0 0 1 56 44" fill="none" stroke="var(--pale)" stroke-width="10"/>
        <path d="M8 44 A24 24 0 0 1 40 21" fill="none" stroke="var(--blue)" stroke-width="10"/>
        <line x1="32" y1="44" x2="44" y2="26" stroke="var(--navy)" stroke-width="4" stroke-linecap="round"/>
        <circle cx="32" cy="44" r="4" fill="var(--navy)"/>
      </svg>
      <div>
        <h3>Try the learnometer!</h3>
        <p>Are you working entrepreneurship-like?</p>
        <span class="feature-btn">Start quiz
          <svg viewBox="0 0 14 14"><rect width="14" height="14" fill="#fff"/><path d="M5 3 l4 4 -4 4" fill="none" stroke="var(--navy)" stroke-width="2"/></svg></span>
      </div>
    </div>
  </section>

  <section class="panel start">
    <div class="panel-tab">Get started!</div>
    <div class="start-cols">
      <div>
        <h3>Teaching plans</h3>
        <ul>
          <li>Lorem ipsum dolor sit amet</li>
          <li>Consectetur adipiscing elit</li>
          <li>Consectetur</li>
          <li>Adipiscing elit dolor sit</li>
          <li>Dolor sit lorem ipsum.</li>
        </ul>
      </div>
      <div class="methods">
        <h3>Methods</h3>
        <ul>
          <li>Café-pedagogikk</li>
          <li>Elevbedrift</li>
          <li>Gründercamp</li>
          <li>Story Line</li>
          <li>Real</li>
        </ul>
      </div>
    </div>
  </section>

</div>
</body>
</html>
```